Letter and Envelope Design For Harborline Realty

Please design a letter and an envelope incorporating our logo (See Attached). We are also launched a business card contest. Since we want them to match, please feel free to submit a design for both the business card and also the letter design and envelope.

Requirements
Must have
• The envelope, the letter and the business cards must match somehow connecting the designs. We want them to have something that holds them together besides the logo.

```html
<!DOCTYPE html>
<html lang="en">
<head>
<meta charset="utf-8">
<title>Harborline Realty Stationery</title>
<link rel="stylesheet" href="https://fonts.googleapis.com/css2?family=Source+Sans+3:wght@400;600&display=swap">
<style>
  :root {
    --navy: #201c6e;
    --slate: #5a5a5c;
    --ink: #444446;
    --paper: #ffffff;
    --ground: #ffffff;
    --rule: #8a8a8c;
  }
  * { margin: 0; padding: 0; box-sizing: border-box; }
  html, body { width: 1200px; height: 1072px; overflow: hidden; background: var(--ground); }
  body { position: relative; font-family: "Source Sans 3", sans-serif; color: var(--ink); }

  .sheet { position: absolute; background: var(--paper); box-shadow: 0 4px 22px rgba(0,0,0,.16); overflow: hidden; }
  .letterhead { left: 58px; top: 58px; width: 734px; height: 974px; }
  .card-front { left: 820px; top: 162px; width: 362px; height: 212px; }
  .card-back { left: 820px; top: 383px; width: 362px; height: 211px; background: var(--slate); }
  .envelope { left: 646px; top: 692px; width: 536px; height: 254px; box-shadow: 0 6px 18px rgba(0,0,0,.16); }
  .envelope-flap { position: absolute; left: 646px; top: 621px; width: 536px; height: 71px; }

  .brand { position: absolute; display: flex; flex-direction: column; align-items: center; }
  .brand-ring { border: 3px solid var(--navy); border-radius: 50%; }
  .brand-name { font-weight: 600; color: var(--navy); text-transform: uppercase; letter-spacing: .12em; white-space: nowrap; text-align: center; line-height: 1.05; }

  .letterhead .brand { left: 36px; top: 30px; width: 200px; }
  .letterhead .brand-ring { width: 76px; height: 76px; }
  .letterhead .brand-name { font-size: 21px; margin-top: 12px; }

  .card-front .brand { left: 16px; top: 57px; width: 132px; }
  .card-front .brand-ring { width: 48px; height: 48px; border-width: 2px; }
  .card-front .brand-name { font-size: 13px; margin-top: 9px; }

  .envelope .brand { left: 12px; top: 15px; width: 126px; }
  .envelope .brand-ring { width: 42px; height: 42px; border-width: 2px; }
  .envelope .brand-name { font-size: 12px; margin-top: 8px; }

  .contact { position: absolute; border-left: 1px solid var(--rule); list-style: none; }
  .contact li { display: flex; align-items: center; white-space: nowrap; }
  .contact svg { flex: none; fill: var(--slate); }

  .letterhead .contact { left: 494px; top: 48px; height: 84px; padding: 2px 0 0 16px; }
  .letterhead .contact li { font-size: 11.5px; height: 21.7px; }
  .letterhead .contact svg { width: 14px; height: 14px; margin-right: 12px; }

  .card-front .contact { left: 171px; top: 30px; height: 127px; padding-left: 12px; }
  .card-front .contact li { font-size: 10.2px; height: 19.4px; }
  .card-front .contact svg { width: 13px; height: 13px; margin-right: 10px; }
  .holder-name { font-size: 16px; font-weight: 600; color: #333; line-height: 1.2; }
  .holder-role { font-size: 11.5px; color: var(--ink); margin-bottom: 22px; }

  .envelope .contact { left: 396px; top: 23px; height: 52px; padding-left: 8px; }
  .envelope .contact li { font-size: 7px; height: 13.5px; }
  .envelope .contact svg { width: 9px; height: 9px; margin-right: 10px; }

  .band { position: absolute; left: 0; right: 0; background: var(--slate); }
  .band-seal { position: absolute; border-radius: 50%; background: var(--paper); border: 2px solid var(--navy); box-shadow: 0 0 0 3px var(--paper); }
  .letterhead .band { top: 910px; height: 22px; }
  .letterhead .band-seal { left: 337px; top: 884px; width: 60px; height: 60px; }
  .card-front .band { top: 187px; height: 10px; }
  .card-front .band-seal { left: 160px; top: 176px; width: 28px; height: 28px; border-width: 1.5px; }
  .envelope .band { top: 226px; height: 16px; }
  .envelope .band-seal { left: 245px; top: 209px; width: 42px; height: 42px; }

  .card-back .brand { left: 0; right: 0; top: 72px; }
  .card-back .brand-ring { width: 40px; height: 40px; border-color: var(--paper); }
  .card-back .brand-name { color: var(--paper); font-size: 14px; margin-top: 10px; }
</style>
</head>
<body>
<svg width="0" height="0" style="position:absolute" aria-hidden="true">
  <defs>
    <symbol id="icon-pin" viewBox="0 0 14 14"><rect width="14" height="14"/><path d="M7 3a2.5 2.5 0 0 0-2.5 2.5C4.5 7.5 7 10.5 7 10.5S9.5 7.5 9.5 5.5A2.5 2.5 0 0 0 7 3z" fill="none" stroke="#fff" stroke-width="1"/></symbol>
    <symbol id="icon-phone" viewBox="0 0 14 14"><rect width="14" height="14"/><path d="M3 6.5c0-2 8-2 8 0v1H9V6.2H5v1.3H3z M4.5 8h5l1 3h-7z" fill="#fff"/></symbol>
    <symbol id="icon-mail" viewBox="0 0 14 14"><rect width="14" height="14"/><rect x="3" y="4.5" width="8" height="5.5" fill="none" stroke="#fff" stroke-width="1"/><path d="M3 4.5l4 3 4-3" fill="none" stroke="#fff" stroke-width="1"/></symbol>
    <symbol id="icon-web" viewBox="0 0 14 14"><rect width="14" height="14"/><circle cx="7" cy="7" r="3.6" fill="none" stroke="#fff" stroke-width=".9"/><path d="M3.4 7h7.2M7 3.4c-2 2.4-2 4.8 0 7.2M7 3.4c2 2.4 2 4.8 0 7.2" fill="none" stroke="#fff" stroke-width=".8"/></symbol>
  </defs>
</svg>

<section class="sheet letterhead" aria-label="Letterhead">
  <div class="brand"><span class="brand-ring"></span><span class="brand-name">Harborline Realty</span></div>
  <ul class="contact">
    <li><svg><use href="#icon-pin"/></svg>Harborline Realty</li>
    <li><svg><use href="#icon-phone"/></svg>312-555-0148</li>
    <li><svg><use href="#icon-mail"/></svg>info@harborline-realty.com</li>
    <li><svg><use href="#icon-web"/></svg>www.harborline-realty.com</li>
  </ul>
  <div class="band"></div>
  <span class="band-seal"></span>
</section>

<section class="sheet card-front" aria-label="Business card front">
  <div class="brand"><span class="brand-ring"></span><span class="brand-name">Harborline Realty</span></div>
  <div class="contact">
    <p class="holder-name">Dana Whitfield</p>
    <p class="holder-role">Realtor</p>
    <ul style="list-style:none">
      <li><svg><use href="#icon-pin"/></svg>Harborline Realty</li>
      <li><svg><use href="#icon-phone"/></svg>312-555-0148</li>
      <li><svg><use href="#icon-mail"/></svg>info@harborline-realty.com</li>
      <li><svg><use href="#icon-web"/></svg>www.harborline-realty.com</li>
    </ul>
  </div>
  <div class="band"></div>
  <span class="band-seal"></span>
</section>

<section class="sheet card-back" aria-label="Business card back">
  <div class="brand"><span class="brand-ring"></span><span class="brand-name">Harborline Realty</span></div>
</section>

<svg class="envelope-flap" viewBox="0 0 536 71" aria-hidden="true">
  <path d="M0 71 L20 10 Q24 0 36 0 H500 Q512 0 516 10 L536 71 Z" fill="var(--slate)"/>
</svg>
<section class="sheet envelope" aria-label="Envelope">
  <div class="brand"><span class="brand-ring"></span><span class="brand-name">Harborline Realty</span></div>
  <ul class="contact">
    <li><svg><use href="#icon-pin"/></svg>Harborline Realty</li>
    <li><svg><use href="#icon-phone"/></svg>312-555-0148</li>
    <li><svg><use href="#icon-mail"/></svg>info@harborline-realty.com</li>
    <li><svg><use href="#icon-web"/></svg>www.harborline-realty.com</li>
  </ul>
  <div class="band"></div>
  <span class="band-seal"></span>
</section>
</body>
</html>
```